Glimmer Step Blog

Need a blog design. I am the first Glimmer Step blogger-very exciting! My first project will be reporting on Twirling Under Lanterns which premieres this Monday-St. Patrick's Day. I am looking for an exciting format to represent my new venture. I will be focusing on ballroom dance fashion-I like creativity and look for something with a cool color scheme, artistic, could be modern or really open for someone to interpret this concept in a creative way. The blog name is GlimStep.

Fashion

```html
<!DOCTYPE html>
<html lang="en">
<head>
<meta charset="utf-8">
<title>Glimmer Step Blog</title>
<link href="https://fonts.googleapis.com/css2?family=Great+Vibes&family=Nunito:wght@700;800&family=Nunito+Sans:wght@600;700&family=Open+Sans:wght@400;600&display=swap" rel="stylesheet">
<style>
:root{
  --sidebar:#e08d1c;
  --sidebar-line:#f3c27c;
  --white:#ffffff;
  --ink:#333333;
  --body:#555555;
  --meta:#666666;
  --rule:#cfcfcf;
  --accent:#e8472b;
  --ribbon:#3a3a3a;
  --ribbon-alt:#8d8d8d;
  --btn-bg:#f2f4f8;
  --btn-border:#c9ced8;
}
*{box-sizing:border-box;margin:0;padding:0}
html,body{width:1200px;height:2782px;overflow:hidden;background:var(--white)}
body{position:relative;font-family:"Open Sans",Arial,sans-serif;color:var(--body)}

.sidebar{position:absolute;left:0;top:0;width:305px;height:2782px;background:var(--sidebar);color:var(--white);text-align:center}
.brand{position:absolute;top:151px;left:0;width:305px;font-family:"Nunito",Arial,sans-serif;font-weight:800;font-size:44px;line-height:44px;letter-spacing:1px;text-transform:uppercase;color:var(--white)}
.divider{position:absolute;left:32px;width:241px;height:24px}
.divider .line{position:absolute;top:11px;height:1px;width:100%;background:var(--sidebar-line)}
.divider .mark{position:absolute;left:104px;top:2px;width:33px;height:20px;border-radius:10px;background:var(--sidebar-line);opacity:.7}
.side-links{position:absolute;top:346px;width:305px;font-family:"Great Vibes",cursive;font-size:27px;line-height:40px}
.welcome{position:absolute;top:540px;width:305px;font-family:"Great Vibes",cursive;font-size:38px;line-height:50px}
.intro{position:absolute;top:730px;left:28px;width:249px;font-family:"Great Vibes",cursive;font-size:23px;line-height:37px}
.copyright{position:absolute;top:1286px;width:305px;font-size:13px;line-height:18px}

.social{position:absolute;top:0;left:914px;display:flex;gap:4px}
.social span{display:block;width:32px;height:41px;background:var(--ribbon-alt);clip-path:polygon(0 0,100% 0,100% 100%,50% 82%,0 100%)}
.social span:first-child{background:var(--ribbon)}

.post{position:absolute;left:369px;width:674px}
.post-title{font-family:"Nunito Sans",Arial,sans-serif;font-weight:700;font-size:30px;line-height:34px;color:var(--ink)}
.meta{display:flex;align-items:center;height:32px;border-top:1px dashed var(--rule);border-bottom:1px dashed var(--rule);font-size:12px;color:var(--meta)}
.meta .comments{margin-left:22px;display:flex;align-items:center;gap:6px}
.share{margin-left:auto;display:flex;gap:8px}
.share span{border:1px solid var(--btn-border);background:var(--btn-bg);border-radius:3px;font-size:10px;line-height:16px;padding:0 5px;color:var(--meta)}
.photo{display:block;margin-top:22px}
.excerpt{margin-top:22px;font-size:13.5px;line-height:18.5px}
.excerpt p+p{margin-top:14px}
.more{display:inline-flex;align-items:center;gap:10px;margin-top:16px;font-size:13.5px;color:var(--accent);text-decoration:none}
.post-divider{position:absolute;left:590px;width:222px;height:40px}
.post-divider .line{position:absolute;top:20px;width:100%;height:1px;background:var(--rule)}
.post-divider .mark{position:absolute;left:92px;top:4px;width:38px;height:32px;border-radius:16px;background:#e3e3e3}
</style>
</head>
<body>

<aside class="sidebar">
  <div class="brand">Glimmer<br>Step</div>
  <div class="divider" style="top:288px" role="img" aria-label="Ornamental flourish divider"><span class="line"></span><span class="mark"></span></div>
  <nav class="side-links"><div>Contact Us</div><div>Follow Us</div></nav>
  <div class="divider" style="top:460px" role="img" aria-label="Ornamental flourish divider"><span class="line"></span><span class="mark"></span></div>
  <h1 class="welcome" style="font-weight:400">Welcome to<br>Glimmer-Step</h1>
  <div class="divider" style="top:666px" role="img" aria-label="Ornamental flourish divider"><span class="line"></span><span class="mark"></span></div>
  <p class="intro">Lorem ipsum dolor sit amet, consec tetur adipiscing elit. In fermentum dolor non augue pretium egestas. Donec sem eros, tincidunt at congue ut, posuere sit amet est. Vivamus scelerisque viverra odio sit amet laoreet. Ut nec neque non justo rutrum tempor lobortis eu ante. Aliquam sagittis, nibh quis auctor. Lorem ipsum dolor sit amet, consec tetur adipiscing elit. In fermentum dolor non augue pretium egestas.</p>
  <div class="divider" style="top:1213px" role="img" aria-label="Ornamental flourish divider"><span class="line"></span><span class="mark"></span></div>
  <p class="copyright">All Right Reserved Copyright © 2014<br>Terms and Conditions</p>
</aside>

<div class="social" aria-label="Social links"><span></span><span></span><span></span><span></span></div>

<article class="post" style="top:72px">
  <h2 class="post-title">Lorem ipsum dolor sit amet, consectetur adipis cing elit Aliquam sagittis</h2>
  <div class="meta" style="margin-top:24px"><span>March 17, 2014,</span><span class="comments"><svg width="11" height="10" viewBox="0 0 11 10"><ellipse cx="5.5" cy="4" rx="5.5" ry="4" fill="#666"/><path d="M2 7 L1 10 L5 7.5Z" fill="#666"/></svg>5 Comments</span>
    <span class="share"><span>Like 3k</span><span>Share 316</span><span>Plus 56</span></span></div>
  <div class="photo" role="img" aria-label="Couples dancing in a ballroom competition" style="width:674px;height:316px;background:linear-gradient(180deg,#3a2418 0%,#6b3d22 45%,#c6803e 100%)"></div>
  <div class="excerpt">
    <p>Lorem ipsum dolor sit amet, consectetur adipiscing elit. In fermentum dolor non augue pretium egestas. Donec sem eros, tincidunt at congue ut, posuere sit amet est. Vivamus scelerisque viverra odio sit amet laoreet. Ut nec neque non justo rutrum tempor lobortis eu ante.</p>
    <p>Aliquam sagittis, nibh quis commodo auctor, risus mauris laoreet lectus, id facilisis libero odio nec enim. Sed id ligula adipiscing purus lacinia aliquet. Sed eu est non nisl vehicula bibendum congue sit amet enim.</p>
  </div>
  <a class="more" href="#">Continue Reading <svg width="14" height="10" viewBox="0 0 14 10"><path d="M0 5H12M8 1L12 5L8 9" stroke="#e8472b" stroke-width="1.6" fill="none"/></svg></a>
</article>
<div class="post-divider" style="top:718px" role="img" aria-label="Ornamental flourish divider"><span class="line"></span><span class="mark"></span></div>

<article class="post" style="top:790px">
  <h2 class="post-title">Lorem ipsum dolor amet, adipis cing aliquam sagittis</h2>
  <div class="meta" style="margin-top:24px"><span>March 17, 2014,</span><span class="comments"><svg width="11" height="10" viewBox="0 0 11 10"><ellipse cx="5.5" cy="4" rx="5.5" ry="4" fill="#666"/><path d="M2 7 L1 10 L5 7.5Z" fill="#666"/></svg>5 Comments</span>
    <span class="share"><span>Like 3k</span><span>Share 316</span><span>Plus 56</span></span></div>
  <div class="photo" role="img" aria-label="Latin dance couple performing on a dark stage" style="margin-left:76px;width:506px;height:763px;background:linear-gradient(180deg,#0c0a0a 0%,#2a1a18 50%,#5a3e30 100%)"></div>
  <div class="excerpt">
    <p>Lorem ipsum dolor sit amet, consectetur adipiscing elit. In fermentum dolor non augue pretium egestas. Donec sem eros, tincidunt at congue ut, posuere sit amet est. Vivamus scelerisque viverra odio sit amet laoreet. Ut nec neque non justo rutrum tempor lobortis eu ante.</p>
    <p>Aliquam sagittis, nibh quis commodo auctor, risus mauris laoreet lectus, id facilisis libero odio nec enim. Sed id ligula adipiscing purus lacinia aliquet. Sed eu est non nisl vehicula bibendum congue sit amet enim.</p>
  </div>
  <a class="more" href="#">Continue Reading <svg width="14" height="10" viewBox="0 0 14 10"><path d="M0 5H12M8 1L12 5L8 9" stroke="#e8472b" stroke-width="1.6" fill="none"/></svg></a>
</article>
<div class="post-divider" style="top:1866px" role="img" aria-label="Ornamental flourish divider"><span class="line"></span><span class="mark"></span></div>

<article class="post" style="top:1946px">
  <h2 class="post-title">Lorem ipsum dolor amet, adipis cing aliquam sagittis</h2>
  <div class="meta" style="margin-top:24px"><span>March 17, 2014,</span><span class="comments"><svg width="11" height="10" viewBox="0 0 11 10"><ellipse cx="5.5" cy="4" rx="5.5" ry="4" fill="#666"/><path d="M2 7 L1 10 L5 7.5Z" fill="#666"/></svg>5 Comments</span>
    <span class="share"><span>Like 3k</span><span>Share 316</span><span>Plus 56</span></span></div>
  <div class="photo" role="img" aria-label="Dance couple in a red dress posing under a spotlight" style="width:674px;height:432px;background:linear-gradient(90deg,#1a0c0c 0%,#8e1a1a 40%,#1e1616 75%,#3c4656 100%)"></div>
  <div class="excerpt">
    <p>Lorem ipsum dolor sit amet, consectetur adipiscing elit. In fermentum dolor non augue pretium egestas. Donec sem eros, tincidunt at congue ut, posuere sit amet est. Vivamus scelerisque viverra odio sit amet laoreet. Ut nec neque non justo rutrum tempor lobortis eu ante.</p>
    <p>Aliquam sagittis, nibh quis commodo auctor, risus mauris laoreet lectus, id facilisis libero odio nec enim. Sed id ligula adipiscing purus lacinia aliquet. Sed eu est non nisl vehicula bibendum congue sit amet enim.</p>
  </div>
  <a class="more" href="#">Continue Reading <svg width="14" height="10" viewBox="0 0 14 10"><path d="M0 5H12M8 1L12 5L8 9" stroke="#e8472b" stroke-width="1.6" fill="none"/></svg></a>
</article>

</body>
</html>
```